Plumbing Company trying to attract new client base for particular works

In need of something to letterbox drop. There is an opportunity to provide "new sewer drains to the new sewer connections on your street".
There will be discounts for pensioners.
We have reviews from clients that are highly satisfied with our work.
Work booked within 1 months of stamped date on flyer will receive a further 10% off.
All work carried out by licences tradespeople.

LOGO will need to be altered to say "tidewell plumbing" rather than contracting

Target Market(s)

Home owners in regional South Australia - age 30+

Industry/Entity Type

It Company

Requirements
Must have
• contact phone number, email, company name,
Nice to have
• images,

```html
<!DOCTYPE html>
<html lang="en">
<head>
<meta charset="utf-8">
<title>Tidewell Plumbing – Sewer Drain Flyer</title>
<link href="https://fonts.googleapis.com/css2?family=Oswald:wght@400;500;600;700&family=Lato:wght@400;700;900&display=swap" rel="stylesheet">
<style>
  :root{
    --yellow:#f7d21b;
    --yellow-deep:#e9b90c;
    --black:#0b0b0b;
    --ink:#161616;
    --white:#ffffff;
  }
  *{margin:0;padding:0;box-sizing:border-box}
  html,body{width:899px;height:1200px;overflow:hidden;background:var(--black)}
  .flyer{position:relative;width:899px;height:1200px;overflow:hidden;
    background:radial-gradient(circle at 40% 55%,#2a2214 0%,#111 45%,var(--black) 75%);
    font-family:'Oswald',sans-serif;color:var(--white)}
  .graphics{position:absolute;inset:0}
  .brand{position:absolute;left:630px;top:168px;width:170px;display:flex;align-items:center;gap:10px}
  .brand-mark{width:26px;height:26px;background:var(--yellow);flex:none}
  .brand-name{font-family:'Oswald',sans-serif;font-weight:600;font-size:19px;line-height:1.05;color:var(--ink);text-transform:uppercase}
  .copy{position:absolute;left:40px;top:700px;width:830px}
  .copy p,.copy h1{white-space:nowrap}
  .intro{font-size:38px;font-weight:500;color:var(--yellow);line-height:1.1;text-transform:uppercase}
  .headline{font-size:46px;font-weight:700;line-height:1.15;text-transform:uppercase}
  .sub{font-size:37px;font-weight:500;color:var(--yellow);line-height:1.15;text-transform:uppercase;letter-spacing:.4px}
  .rule{height:2px;background:var(--white);margin:10px 0 10px;width:800px}
  .licence{font-size:24px;font-weight:600;text-transform:uppercase;line-height:1.3}
  .licence strong{font-size:33px;color:var(--yellow);font-weight:600}
  .offer{font-family:'Lato',sans-serif;font-size:20px;color:var(--yellow);text-transform:uppercase;line-height:1.35;margin-top:8px}
  .offer b{color:var(--white);font-weight:900}
  .values{position:absolute;left:0;top:1002px;height:48px;width:800px;background:var(--yellow);
    clip-path:polygon(0 0,100% 0,94% 100%,0 100%);
    display:flex;align-items:center;padding-left:58px;color:var(--ink);font-size:27px;font-weight:500;text-transform:uppercase;letter-spacing:.3px;gap:13px;white-space:nowrap}
  .company{position:absolute;left:58px;top:1092px;display:flex;align-items:center;gap:14px;font-size:21px;font-weight:600;text-transform:uppercase}
  .company::after{content:"";width:190px;height:2px;background:var(--white)}
  .contact{position:absolute;left:58px;top:1142px;display:flex;align-items:center;gap:28px;font-size:20px;color:var(--yellow);text-transform:uppercase;white-space:nowrap}
  .contact span{display:flex;align-items:center;gap:10px}
  .contact svg{fill:var(--white)}
  .licences{position:absolute;right:34px;top:1130px;text-align:right;font-family:'Lato',sans-serif;font-weight:700;font-size:11.5px;color:var(--ink);line-height:1.3}
</style>
</head>
<body>
<main class="flyer">
  <svg class="graphics" width="899" height="1200" viewBox="0 0 899 1200">
    <defs>
      <linearGradient id="job-site" x1="0" y1="0" x2="1" y2="1">
        <stop offset="0" stop-color="#8a5a44"/>
        <stop offset=".45" stop-color="#b23a22"/>
        <stop offset="1" stop-color="#4a3a2c"/>
      </linearGradient>
      <linearGradient id="trench" x1="0" y1="0" x2="0" y2="1">
        <stop offset="0" stop-color="#6f7a4a"/>
        <stop offset="1" stop-color="#5b3b24"/>
      </linearGradient>
    </defs>

    <polygon points="540,1200 899,846 899,1200" fill="var(--yellow)"/>
    <polygon points="522,1200 899,828 899,838 532,1200" fill="var(--white)"/>

    <polygon points="800,0 899,0 899,14 814,0" fill="var(--yellow)"/>
    <polygon points="860,60 899,22 899,118 845,172" fill="var(--yellow)"/>
    <rect x="800" y="300" width="200" height="200" rx="36" fill="var(--yellow)" transform="rotate(45 900 400)"/>

    <path d="M0 0 H640 L485 470 Q468 515 415 518 L0 580 Z" fill="var(--white)"/>
    <path d="M0 0 H610 L462 450 Q448 490 400 494 L0 556 Z" fill="url(#job-site)" role="img" aria-label="Photo of a tradesman operating a red mini excavator beside a brick house"/>
    <path d="M0 612 Q260 560 455 525 Q490 518 505 500" fill="none" stroke="var(--yellow)" stroke-width="20"/>
    <path d="M0 640 Q260 590 470 550" fill="none" stroke="var(--yellow)" stroke-width="5"/>

    <rect x="600" y="75" width="220" height="220" rx="40" fill="var(--black)" transform="rotate(45 710 185)"/>
    <rect x="615" y="90" width="190" height="190" rx="32" fill="var(--white)" transform="rotate(45 710 185)"/>

    <rect x="452" y="252" width="196" height="196" rx="34" fill="var(--black)" transform="rotate(45 550 350)"/>
    <rect x="462" y="262" width="176" height="176" rx="28" fill="url(#trench)" stroke="var(--yellow)" stroke-width="5" transform="rotate(45 550 350)" role="img" aria-label="Photo of an open sewer trench in a garden"/>
    <rect x="605" y="415" width="210" height="210" rx="36" fill="var(--black)" transform="rotate(45 710 520)"/>
    <rect x="616" y="426" width="188" height="188" rx="30" fill="#6b4a30" stroke="var(--yellow)" stroke-width="5" transform="rotate(45 710 520)" role="img" aria-label="Photo of a new drain pipe laid in a dug trench"/>
  </svg>

  <div class="brand">
    <span class="brand-mark"></span>
    <span class="brand-name">Tidewell<br>Plumbing</span>
  </div>

  <section class="copy">
    <p class="intro">We're here to help you</p>
    <h1 class="headline">Replace or renew your sewer drain</h1>
    <p class="sub">or design a septic system for your home</p>
    <div class="rule"></div>
    <p class="licence">All work carried out by <strong>Licences Tradespeople</strong></p>
    <p class="offer">Pensioner discounts apply- receive a further <b>10% off</b><br>if booked within <b>1 month</b> of the stamped date on flyer</p>
  </section>

  <div class="values">Reliable <span>|</span> Trustworthy <span>|</span> Affordable <span>|</span> Experienced</div>

  <p class="company">Tidewell Plumbing Pty Ltd</p>
  <div class="contact">
    <span><svg width="18" height="18" viewBox="0 0 24 24"><path d="M6.6 10.8a15.1 15.1 0 0 0 6.6 6.6l2.2-2.2a1 1 0 0 1 1-.25 11.4 11.4 0 0 0 3.6.57 1 1 0 0 1 1 1V20a1 1 0 0 1-1 1A17 17 0 0 1 3 4a1 1 0 0 1 1-1h3.5a1 1 0 0 1 1 1 11.4 11.4 0 0 0 .57 3.6 1 1 0 0 1-.25 1z"/></svg>0491570156</span>
    <span><svg width="22" height="16" viewBox="0 0 22 16"><path d="M0 0h22v16H0z" fill="none" stroke="#fff" stroke-width="2"/><path d="M1 1l10 8 10-8" fill="none" stroke="#fff" stroke-width="2"/></svg>office@tidewellplumbing.com.au</span>
  </div>
  <p class="licences">ABN : 51824753556<br>BLD: 318406, PGE: 274519</p>
</main>
</body>
</html>
```